Change of trading name, rebrand

existing website to be updated with new theme and logo. existing website is
www.harlowbrentmere.com.au
Industry/Entity Type
Construction
Coding
Coded - Design and coding required
Number of Pages Required
5+ page
Requirements
Must have
- be mobile phone friendly

```html
<!DOCTYPE html>
<html lang="en">
<head>
<meta charset="utf-8">
<title>HBR Heavy Equipment – Plant Hire</title>
<meta name="viewport" content="width=1200">
<link href="https://fonts.googleapis.com/css2?family=Montserrat:wght@400;500;600;700;800;900&display=swap" rel="stylesheet">
<style>
:root{
  --navy:#252a72;
  --navy-dark:#1c2060;
  --navy-deep:#14173f;
  --ink:#1b1b1b;
  --grey:#6b6b6b;
  --line:#e4e4ea;
  --pale:#f3f4fa;
  --white:#ffffff;
}
*{box-sizing:border-box;margin:0;padding:0}
html,body{width:1200px;height:5277px;overflow:hidden}
body{font-family:"Montserrat",sans-serif;color:var(--ink);background:var(--white)}
a{color:inherit;text-decoration:none}
.wrap{width:1200px;position:relative}
.btn{display:inline-flex;align-items:center;gap:10px;font-weight:700;font-size:13px;letter-spacing:.5px;text-transform:uppercase;background:var(--navy);color:#fff;padding:10px 22px;border:2px solid #fff;outline:2px solid var(--navy)}
.btn svg{width:12px;height:12px}
.section-title{font-weight:800;font-size:42px;color:var(--navy);text-align:center;text-transform:uppercase;line-height:1.3}

/* top bar */
.topbar{height:74px;background:var(--navy);display:flex;justify-content:space-between;align-items:center;padding:0 104px;color:#fff;position:relative}
.topbar .info{display:flex;align-items:center;gap:14px;font-size:13px;line-height:1.35}
.topbar .info b{font-weight:700;display:block;font-size:12px}
.topbar .ico{width:36px;height:36px;border:2px solid #fff;display:flex;align-items:center;justify-content:center}
.topbar .ico svg{width:18px;height:18px}
.brand-tab{position:absolute;left:50%;top:0;transform:translateX(-50%);width:184px;height:78px;background:#fff;clip-path:polygon(0 0,100% 0,86% 100%,14% 100%);display:flex;align-items:center;justify-content:center;gap:8px}
.brand-tab .sq{width:14px;height:14px;background:var(--navy)}
.brand-tab span{font-weight:900;font-size:30px;color:var(--navy);letter-spacing:1px}

/* nav */
.nav{height:73px;display:flex;align-items:center;padding-left:136px;gap:40px;font-size:14px;font-weight:500;border-bottom:1px solid var(--line)}
.nav a.active{font-weight:700;color:var(--navy)}

/* hero */
.hero{height:509px;position:relative;background:linear-gradient(100deg,#2a2620 0%,#4a3d2c 40%,#8a7a55 65%,#b0a27a 100%);color:#fff}
.hero .pad{position:absolute;left:104px;top:110px}
.hero .kicker{font-size:26px;font-weight:400;letter-spacing:.5px}
.hero h1{font-weight:900;font-size:46px;line-height:1.3;margin-top:8px}
.hero p{font-size:15px;line-height:1.9;margin-top:10px;width:380px}
.hero .btn{margin-top:18px;background:var(--navy);outline:none;border:2px solid #fff}
.arrow-round{position:absolute;width:38px;height:38px;border-radius:50%;display:flex;align-items:center;justify-content:center}
.arrow-round svg{width:14px;height:14px}
.arrow-round.light{background:rgba(255,255,255,.55)}
.arrow-round.dark{background:var(--navy)}

/* about */
.about{height:481px;text-align:center;padding-top:72px;background:radial-gradient(ellipse at 50% 45%,#f2f2f4 0%,#fff 60%)}
.about .lead{font-size:16px;font-weight:500;line-height:1.7;width:700px;margin:22px auto 0}
.about .body{font-size:14px;color:var(--grey);line-height:1.95;width:760px;margin:12px auto 0}
.about .btn{margin-top:22px}

/* features band */
.features{height:303px;background:var(--navy-dark);display:flex;justify-content:center;align-items:center;gap:12px}
.feature{width:180px;height:186px;background:var(--navy);transform:skewX(-14deg);display:flex;align-items:center;justify-content:center}
.feature .in{transform:skewX(14deg);text-align:center;color:#fff;font-size:17px;line-height:1.5;font-weight:500;text-transform:uppercase}
.feature svg{width:52px;height:52px;margin-bottom:12px}

/* plant hire */
.plant{height:865px;background:var(--pale);padding-top:80px;position:relative}
.tabs{display:flex;justify-content:center;gap:16px;margin-top:28px}
.tab{width:186px;height:142px;background:#fff;display:flex;flex-direction:column;align-items:center;justify-content:center;text-align:center;font-size:17px;line-height:1.45;font-weight:500;text-transform:uppercase;box-shadow:0 2px 8px rgba(0,0,0,.06)}
.tab svg{width:48px;height:34px;margin-bottom:10px}
.cards{display:flex;justify-content:center;gap:40px;margin-top:42px}
.card{width:300px;height:422px;background:#fff;padding:10px;text-align:center;box-shadow:0 2px 10px rgba(0,0,0,.07);position:relative}
.card .photo{height:206px}
.card .badge{width:60px;height:60px;border-radius:50%;background:var(--navy);border:4px solid #fff;margin:-30px auto 0;position:relative;display:flex;align-items:center;justify-content:center}
.card .badge svg{width:32px;height:24px}
.card h3{font-size:28px;font-weight:700;line-height:1.3;margin-top:10px}
.card p{font-size:15px;color:var(--grey);line-height:1.6;margin-top:10px;padding:0 20px}
.card .btn{margin-top:18px;font-size:12px;padding:8px 18px}
.side-arrow{position:absolute;width:14px;height:14px}

/* projects */
.projects{height:536px;position:relative}
.projects .photo{position:absolute;left:110px;top:96px;width:486px;height:334px;background:linear-gradient(160deg,#8a9a7a 0%,#a58a62 40%,#7a5a38 100%)}
.projects .text{position:absolute;left:696px;top:104px}
.projects h2{font-weight:800;font-size:42px;color:var(--navy)}
.projects .num{font-weight:800;font-size:34px;color:var(--navy);margin-top:26px}
.projects .pname{font-weight:700;font-size:19px;margin-top:18px}
.projects .meta{display:flex;align-items:center;gap:14px;font-size:19px;margin-top:22px}
.projects .meta svg{width:20px;height:20px}
.projects .view{display:flex;align-items:center;gap:18px;font-size:14px;font-weight:700;color:var(--navy);text-decoration:underline;margin-top:24px}

/* safety */
.safety{height:734px;position:relative;background:linear-gradient(180deg,var(--pale) 0%,#fff 40%)}
.safety .section-title{padding-top:56px}
.machine{position:absolute;left:378px;top:245px;width:440px;height:210px;background:linear-gradient(90deg,#2a2a2a,#555,#2a2a2a);border-radius:6px;opacity:.9}
.value{position:absolute;display:flex;align-items:center;gap:12px;font-weight:700;font-size:29px}
.vbox{width:78px;height:78px;border:2px solid var(--navy);padding:5px}
.vbox div{width:100%;height:100%;background:var(--navy);display:flex;align-items:center;justify-content:center}
.vbox svg{width:38px;height:38px}

/* quote */
.quote{height:455px;position:relative;background:linear-gradient(90deg,#1e1e1e 0%,#2f2a26 55%,#6a6c72 75%,#8a8c94 100%)}
.quote .person{position:absolute;right:0;top:0;width:540px;height:455px;background:linear-gradient(110deg,rgba(60,70,130,0) 0%,#5a6aa0 30%,#c9ccd4 70%,#e8e8ea 100%)}
.quote h2{position:absolute;left:104px;top:42px;color:#fff;font-weight:800;font-size:42px}
.qform{position:absolute;left:104px;top:110px;width:576px;display:grid;grid-template-columns:1fr 1fr;gap:14px 14px}
.qform .f{background:#fff;height:52px;font-size:15px;color:#777;padding:16px 22px}
.qform .f.full{grid-column:1/3;height:122px}
.qform .btn{grid-column:1/2;justify-self:start;background:#fff;color:var(--ink);outline:none;border:2px solid #fff;box-shadow:0 0 0 2px #222 inset;font-size:13px;margin-top:6px}

/* partners */
.partners{height:467px;position:relative;padding-top:128px}
.logos{display:flex;justify-content:center;gap:26px;margin-top:52px}
.logo-slot{width:176px;height:96px;background:#fff;box-shadow:0 2px 10px rgba(0,0,0,.07);display:flex;align-items:center;justify-content:center}
.logo-slot div{width:96px;height:42px;border-radius:6px;background:#dcdde6}

/* contact band */
.contact{height:282px;background:var(--navy);color:#fff;position:relative}
.contact .rule{position:absolute;left:134px;right:134px;top:108px;height:1px;background:rgba(255,255,255,.6)}
.citem{position:absolute;top:70px;width:240px;text-align:center}
.citem .cbox{width:78px;height:78px;background:#fff;margin:0 auto;display:flex;align-items:center;justify-content:center;border:4px solid var(--navy);outline:2px solid #fff}
.citem .cbox svg{width:38px;height:38px}
.citem h4{font-weight:700;font-size:18px;margin-top:22px;text-transform:uppercase}
.citem p{font-size:18px;line-height:1.6;margin-top:8px}

/* footer */
.footer{height:498px;background:linear-gradient(180deg,#1a1c2e 0%,#24273a 100%);color:#fff;position:relative}
.footer h5{font-weight:700;font-size:17px;text-transform:uppercase}
.fcol{position:absolute;top:108px}
.fcol ul{list-style:none;margin-top:26px}
.fcol li{font-size:15px;text-transform:uppercase;line-height:43px;display:flex;align-items:center;gap:18px}
.fcol.bullets li::before{content:"";width:8px;height:8px;border-radius:50%;background:#fff}
.copy{position:absolute;bottom:22px;width:100%;text-align:center;font-size:14px}
</style>
</head>
<body>
<div class="wrap">

<header class="topbar">
  <div class="info">
    <span class="ico"><svg viewBox="0 0 24 24" fill="none" stroke="#fff" stroke-width="2"><path d="M12 22s7-7 7-12a7 7 0 0 0-14 0c0 5 7 12 7 12z"/><circle cx="12" cy="10" r="2.5"/></svg></span>
    <span><b>LOCATE US :</b>18 Wattle Rd,Kenmore QLD 4069</span>
  </div>
  <a class="brand-tab" href="#"><i class="sq"></i><span>HBR</span></a>
  <div class="info">
    <span class="ico"><svg viewBox="0 0 24 24" fill="#fff"><path d="M6.6 10.8a15 15 0 0 0 6.6 6.6l2.2-2.2c.3-.3.7-.4 1-.2 1.1.4 2.3.6 3.6.6.6 0 1 .4 1 1V20c0 .6-.4 1-1 1A17 17 0 0 1 3 4c0-.6.4-1 1-1h3.5c.6 0 1 .4 1 1 0 1.3.2 2.5.6 3.6.1.3 0 .7-.2 1z"/></svg></span>
    <span><b>CALL US :</b>1300 555 014</span>
  </div>
</header>

<nav class="nav">
  <a class="active" href="#">HOME</a><a href="#">ABOUT US</a><a href="#">PLANT HIRE</a><a href="#">MAJOR PROJECT SNAPSHOT</a><a href="#">POLICIES</a><a href="#">JOBS</a><a href="#">CONTACT US</a>
</nav>

<section class="hero" role="img" aria-label="Yellow excavator loading a dump truck on a work site">
  <div class="pad">
    <div class="kicker">THE MOST EXTENSIVE</div>
    <h1>PLANT HIRE FLEETS<br>IN QUEENSLAND</h1>
    <p>Contact us directly so that we can assist you with your plant hire needs</p>
    <a class="btn" href="#">Plant Hire <svg viewBox="0 0 12 12" fill="none" stroke="#fff" stroke-width="2"><path d="M1 6h9M7 3l3 3-3 3"/></svg></a>
  </div>
  <span class="arrow-round light" style="left:44px;top:236px"><svg viewBox="0 0 14 14" fill="none" stroke="#fff" stroke-width="2"><path d="M9 2 4 7l5 5"/></svg></span>
  <span class="arrow-round dark" style="right:38px;top:236px"><svg viewBox="0 0 14 14" fill="none" stroke="#fff" stroke-width="2"><path d="m5 2 5 5-5 5"/></svg></span>
</section>

<section class="about">
  <h2 class="section-title">About HBR Heavy<br>Equipment</h2>
  <p class="lead">Harlow Brentmere Resources Pty Ltd trading as HBR Heavy Equipment is a privately owned company that was established in 2010</p>
  <p class="body">Harlow Brentmere Resources Pty Ltd trading as HBR Heavy Equipment is a privately owned company that was established in 2010. Our founder saw a need in the market for a plant and equipment supplier who was committed to the successful delivery of client's projects</p>
  <a class="btn" href="#">Read More <svg viewBox="0 0 12 12" fill="none" stroke="#fff" stroke-width="2"><path d="M1 6h9M7 3l3 3-3 3"/></svg></a>
</section>

<section class="features">
  <div class="feature"><div class="in"><svg viewBox="0 0 48 48" fill="none" stroke="#fff" stroke-width="2"><circle cx="24" cy="20" r="10"/><path d="M18 29l-4 14 10-5 10 5-4-14"/><path d="M24 15l1.5 3 3.3.4-2.4 2.3.6 3.3-3-1.6-3 1.6.6-3.3-2.4-2.3 3.3-.4z"/></svg><br>20+<br>Years of<br>Experience</div></div>
  <div class="feature"><div class="in"><svg viewBox="0 0 48 48" fill="none" stroke="#fff" stroke-width="2"><rect x="6" y="20" width="22" height="14"/><path d="M28 24h8l6 6v4H28z"/><circle cx="13" cy="37" r="3"/><circle cx="36" cy="37" r="3"/><path d="M10 20V10h10v10"/></svg><br>100+<br>Machines in<br>Fleet</div></div>
  <div class="feature"><div class="in"><svg viewBox="0 0 48 48" fill="none" stroke="#fff" stroke-width="2"><path d="M18 6h8v10l8 8 4 16H10l4-16 4-8z"/></svg><br>One of QLD's<br>Largest<br>Suppliers</div></div>
  <div class="feature"><div class="in"><svg viewBox="0 0 48 48" fill="none" stroke="#fff" stroke-width="2"><circle cx="24" cy="16" r="7"/><path d="M16 10h16M10 42c0-9 6-14 14-14s14 5 14 14z"/><path d="M20 32h8v6h-8z"/></svg><br>Onsite<br>Servicing</div></div>
  <div class="feature"><div class="in"><svg viewBox="0 0 48 48" fill="none" stroke="#fff" stroke-width="2"><circle cx="24" cy="24" r="7"/><path d="M24 6v6M24 36v6M6 24h6M36 24h6M11 11l4 4M33 33l4 4M11 37l4-4M33 15l4-4"/><circle cx="24" cy="24" r="13"/></svg><br>Custom<br>Machine<br>Attachments</div></div>
</section>

<section class="plant">
  <h2 class="section-title">Plant Hire</h2>
  <svg class="side-arrow" style="left:60px;top:214px" viewBox="0 0 14 14" fill="none" stroke="#666" stroke-width="2"><path d="M9 2 4 7l5 5"/></svg>
  <svg class="side-arrow" style="right:60px;top:214px" viewBox="0 0 14 14" fill="none" stroke="#222" stroke-width="2"><path d="m5 2 5 5-5 5"/></svg>
  <div class="tabs">
    <div class="tab"><svg viewBox="0 0 48 34" fill="none" stroke="#252a72" stroke-width="2"><rect x="4" y="16" width="20" height="10"/><path d="M24 18l10-12 10 8-4 6"/><rect x="4" y="26" width="20" height="6" rx="3"/></svg>Excavators &amp;<br>Diggers</div>
    <div class="tab"><svg viewBox="0 0 48 34" fill="none" stroke="#252a72" stroke-width="2"><rect x="10" y="8" width="14" height="12"/><rect x="6" y="20" width="26" height="10" rx="5"/><path d="M32 14h8v16"/></svg>Dozers</div>
    <div class="tab"><svg viewBox="0 0 48 34" fill="none" stroke="#252a72" stroke-width="2"><rect x="14" y="6" width="14" height="12"/><rect x="6" y="18" width="30" height="12" rx="4"/><path d="M36 12h6v18"/></svg>Swamp<br>Dozers</div>
    <div class="tab"><svg viewBox="0 0 48 34" fill="none" stroke="#252a72" stroke-width="2"><rect x="4" y="10" width="10" height="12"/><path d="M14 14h28v8H14z"/><circle cx="10" cy="26" r="3"/><circle cx="30" cy="26" r="3"/><circle cx="38" cy="26" r="3"/></svg>Articulated<br>Dump</div>
    <div class="tab"><svg viewBox="0 0 48 34" fill="none" stroke="#252a72" stroke-width="2"><path d="M4 20h40"/><rect x="30" y="8" width="10" height="12"/><circle cx="8" cy="25" r="3"/><circle cx="36" cy="25" r="3"/><path d="M16 20v6h10"/></svg>Road<br>Graders</div>
  </div>
  <span class="arrow-round" style="left:44px;top:544px;background:#c9cad2"><svg viewBox="0 0 14 14" fill="none" stroke="#fff" stroke-width="2"><path d="M9 2 4 7l5 5"/></svg></span>
  <span class="arrow-round dark" style="right:42px;top:544px"><svg viewBox="0 0 14 14" fill="none" stroke="#fff" stroke-width="2"><path d="m5 2 5 5-5 5"/></svg></span>
  <div class="cards">
    <article class="card">
      <div class="photo" role="img" aria-label="Mini excavator on a trailer" style="background:linear-gradient(160deg,#7d8a6c,#c7a342 55,#3e3a33)"></div>
      <div class="badge"><svg viewBox="0 0 48 34" fill="none" stroke="#fff" stroke-width="2.5"><rect x="4" y="16" width="20" height="10"/><path d="M24 18l10-12 10 8-4 6"/></svg></div>
      <h3>Excavators and<br>Diggers for Hire</h3>
      <p>HBR Heavy Equipment has one of the largest fleet</p>
      <a class="btn" href="#">Read More <svg viewBox="0 0 12 12" fill="none" stroke="#fff" stroke-width="2"><path d="M1 6h9M7 3l3 3-3 3"/></svg></a>
    </article>
    <article class="card">
      <div class="photo" role="img" aria-label="Dozer working on a cleared site" style="background:linear-gradient(170deg,#a8b3b8 0%,#8a8a70 45%,#8a6e4e 100%)"></div>
      <div class="badge"><svg viewBox="0 0 48 34" fill="none" stroke="#fff" stroke-width="2.5"><rect x="10" y="8" width="14" height="12"/><rect x="6" y="20" width="26" height="10" rx="5"/></svg></div>
      <h3>Dozers for<br>Hire</h3>
      <p>Bulldozers of all sizes available for hire from</p>
      <a class="btn" href="#">Read More <svg viewBox="0 0 12 12" fill="none" stroke="#fff" stroke-width="2"><path d="M1 6h9M7 3l3 3-3 3"/></svg></a>
    </article>
    <article class="card">
      <div class="photo" role="img" aria-label="Yellow swamp dozer" style="background:linear-gradient(160deg,#d8d8d8 0%,#c8a030 50%,#6a5a3a 100%)"></div>
      <div class="badge"><svg viewBox="0 0 48 34" fill="none" stroke="#fff" stroke-width="2.5"><rect x="14" y="6" width="14" height="12"/><rect x="6" y="18" width="30" height="12" rx="4"/></svg></div>
      <h3>Swamp Dozers<br>for Hire</h3>
      <p>HBR Heavy Equipment has one of the largest fleet</p>
      <a class="btn" href="#">Read More <svg viewBox="0 0 12 12" fill="none" stroke="#fff" stroke-width="2"><path d="M1 6h9M7 3l3 3-3 3"/></svg></a>
    </article>
  </div>
</section>

<section class="projects">
  <div class="photo" role="img" aria-label="Dozer pushing soil on a project site"></div>
  <span class="arrow-round" style="left:86px;top:244px;background:#bfc0c8"><svg viewBox="0 0 14 14" fill="none" stroke="#fff" stroke-width="2"><path d="M9 2 4 7l5 5"/></svg></span>
  <span class="arrow-round dark" style="left:582px;top:244px"><svg viewBox="0 0 14 14" fill="none" stroke="#fff" stroke-width="2"><path d="m5 2 5 5-5 5"/></svg></span>
  <div class="text">
    <h2>OUR PROJECTS</h2>
    <div class="num">01.</div>
    <div class="pname">RIVERBEND ENHANCEMENT PROJECT</div>
    <div class="meta"><svg viewBox="0 0 20 20" fill="none" stroke="#252a72" stroke-width="1.6"><circle cx="10" cy="6" r="4"/><path d="M2 19c0-5 4-7 8-7s8 2 8 7"/></svg>Client – Brookvale Contractors</div>
    <div class="meta"><svg viewBox="0 0 20 20" fill="none" stroke="#252a72" stroke-width="1.6"><rect x="2" y="4" width="16" height="14"/><path d="M2 8h16M6 2v4M14 2v4"/></svg>Commencement Year – 2017</div>
    <a class="view" href="#">VIEW PROJECT <svg width="14" height="12" viewBox="0 0 14 12" fill="none" stroke="#252a72" stroke-width="2"><path d="M1 6h11M9 3l3 3-3 3"/></svg></a>
  </div>
</section>

<section class="safety">
  <h2 class="section-title">Safety and<br>Compliance</h2>
  <div class="machine" role="img" aria-label="Line drawing of a bulldozer and an excavator"></div>
  <div class="value" style="left:225px;top:140px">Safety<span class="vbox"><div><svg viewBox="0 0 38 38" fill="none" stroke="#fff" stroke-width="2"><path d="M19 4l12 5v9c0 8-5 13-12 16C12 31 7 26 7 18V9z"/><path d="m13 19 4 4 8-8"/></svg></div></span></div>
  <div class="value" style="left:796px;top:140px"><span class="vbox"><div><svg viewBox="0 0 38 38" fill="none" stroke="#fff" stroke-width="2"><circle cx="19" cy="19" r="5"/><circle cx="19" cy="19" r="12"/><path d="M19 4v4M19 30v4M4 19h4M30 19h4"/></svg></div></span>Diverse</div>
  <div class="value" style="left:105px;top:302px">Experience<span class="vbox"><div><svg viewBox="0 0 38 38" fill="none" stroke="#fff" stroke-width="2"><circle cx="19" cy="16" r="8"/><path d="M14 23l-3 11 8-4 8 4-3-11"/></svg></div></span></div>
  <div class="value" style="left:852px;top:302px"><span class="vbox"><div><svg viewBox="0 0 38 38" fill="none" stroke="#fff" stroke-width="2"><path d="m8 30 14-14M22 8l8 8-4 4-8-8zM8 8l22 22"/></svg></div></span>Technology</div>
  <div class="value" style="left:154px;top:490px">Team Work<span class="vbox"><div><svg viewBox="0 0 38 38" fill="none" stroke="#fff" stroke-width="2"><circle cx="12" cy="14" r="4"/><circle cx="26" cy="14" r="4"/><path d="M5 30c0-5 3-8 7-8s7 3 7 8M19 30c0-5 3-8 7-8s7 3 7 8"/></svg></div></span></div>
  <div class="value" style="left:796px;top:490px"><span class="vbox"><div><svg viewBox="0 0 38 38" fill="none" stroke="#fff" stroke-width="2"><circle cx="19" cy="16" r="8"/><path d="M15 26h8M16 30h6"/></svg></div></span>Innovation</div>
  <div class="value" style="left:485px;top:540px;flex-direction:column;gap:14px"><span class="vbox"><div><svg viewBox="0 0 38 38" fill="none" stroke="#fff" stroke-width="2"><circle cx="19" cy="19" r="12"/><path d="m13 19 4 4 8-8"/></svg></div></span>Quality Matters</div>
</section>

<section class="quote">
  <div class="person" role="img" aria-label="Company owner standing beside a branded work vehicle"></div>
  <h2>GET A FREE QUOTE</h2>
  <form class="qform">
    <div class="f">First Name</div>
    <div class="f">Last Name</div>
    <div class="f">Email</div>
    <div class="f">Phone</div>
    <div class="f full">Message</div>
    <span class="btn">Submit Now <svg viewBox="0 0 12 12" fill="none" stroke="#222" stroke-width="2"><path d="M1 6h9M7 3l3 3-3 3"/></svg></span>
  </form>
</section>

<section class="partners">
  <h2 class="section-title">Our Partner</h2>
  <span class="arrow-round" style="left:40px;top:248px;background:#c9cad2"><svg viewBox="0 0 14 14" fill="none" stroke="#fff" stroke-width="2"><path d="M9 2 4 7l5 5"/></svg></span>
  <span class="arrow-round dark" style="right:42px;top:248px"><svg viewBox="0 0 14 14" fill="none" stroke="#fff" stroke-width="2"><path d="m5 2 5 5-5 5"/></svg></span>
  <div class="logos">
    <div class="logo-slot"><div></div></div>
    <div class="logo-slot"><div></div></div>
    <div class="logo-slot"><div></div></div>
    <div class="logo-slot"><div></div></div>
    <div class="logo-slot"><div></div></div>
  </div>
</section>

<section class="contact">
  <div class="rule"></div>
  <div class="citem" style="left:157px">
    <div class="cbox"><svg viewBox="0 0 24 24" fill="none" stroke="#252a72" stroke-width="1.6"><path d="M12 22s7-7 7-12a7 7 0 0 0-14 0c0 5 7 12 7 12z"/><circle cx="12" cy="10" r="2.5"/></svg></div>
    <h4>Our Location</h4><p>18 WATTLE RD, KENMORE<br>QLD 4069</p>
  </div>
  <div class="citem" style="left:480px">
    <div class="cbox"><svg viewBox="0 0 24 24" fill="none" stroke="#252a72" stroke-width="1.6"><path d="M6.6 10.8a15 15 0 0 0 6.6 6.6l2.2-2.2c.3-.3.7-.4 1-.2 1.1.4 2.3.6 3.6.6.6 0 1 .4 1 1V20c0 .6-.4 1-1 1A17 17 0 0 1 3 4c0-.6.4-1 1-1h3.5c.6 0 1 .4 1 1 0 1.3.2 2.5.6 3.6.1.3 0 .7-.2 1z"/></svg></div>
    <h4>Our Phone</h4><p>1300 555 014</p>
  </div>
  <div class="citem" style="left:778px">
    <div class="cbox"><svg viewBox="0 0 24 24" fill="none" stroke="#252a72" stroke-width="1.6"><rect x="6" y="3" width="12" height="6"/><rect x="3" y="9" width="18" height="9"/><rect x="7" y="14" width="10" height="7"/></svg></div>
    <h4>Our Fax</h4><p>07 5550 1234</p>
  </div>
</section>

<footer class="footer">
  <div class="fcol bullets" style="left:107px">
    <h5>Our Plant</h5>
    <ul><li>Excavators and Diggers</li><li>Dozers</li><li>Swamp Dozers</li><li>Articulated Dump Trucks</li><li>Road Graders</li></ul>
  </div>
  <div class="fcol bullets" style="left:430px;top:128px">
    <ul style="margin-top:26px"><li>Bobcats and Skid Steer Loaders</li><li>Water Carts and Tankers</li><li>Backhoes</li><li>Soil Compactors</li><li>Loaders</li></ul>
  </div>
  <div class="fcol" style="left:840px">
    <h5>Quick Link</h5>
    <ul><li>Home</li><li>About Us</li><li>Plant Hire</li><li>Major Project Snapshot</li><li>Policies</li><li>JobsContact Us</li></ul>
  </div>
  <div class="copy">© 2024 HBR. ALL RIGHT RESERVED</div>
</footer>

</div>
</body>
</html>
```